CalmPeak Nurses' Manifesto

Design a manifesto to inspire and motivate nurses to work at minimum standards of excellence in their nursing practice.

The manifesto will become a feature of our website, at conferences, workshops and retreats. It will also be featured on other marketing tools.

Primary Market:
Nurses and/or other healthcare professionals (specifically Doctors, Occupational Therapists, Psychologists and Social Workers).

However the manifesto is equally applicable to all nurses and healthcare professionals from new graduates to very experienced senior clinicians, administration officers,managers and healthcare executive personnel.

Mainly females and primarily 35 to 65 years old, which suggests people in this target age group have extensive experience, but have become jaded'.

The purpose of our business is to assist healthcare professionals, primarily nurses, to maintain their enthusiasm and excellence in service provision, for their benefit as well as the benefit of the clients.

I have attached:
File 1: Copy Samples and examples: which has the copy for the manifesto, examples that appeal to us and our 3 attempts.
File 2: Our colour Spec Sheet, HOWEVER the colours are not necessary limited to these colours. These colours are not in the logo that will be on the manifesto. The colours on the logo attached can/or also be used.
File 3: Prototype logo. The final logo will be available within 3 to 4 days.

Industry/Entity Type

Healthcare

Requirements
Must have
• Must use the copy as per the attached file.

It should be contemporary, eye catching and motivational.

Should not have
• MUST BE EASY TO READ. Each line MUST be clearly defined from each other.

```html
<!DOCTYPE html>
<html lang="en">
<head>
<meta charset="utf-8">
<title>CalmPeak Nurses' Manifesto</title>
<link rel="stylesheet" href="https://fonts.googleapis.com/css2?family=Righteous&family=Oswald:wght@300;400;600&family=Comfortaa:wght@400;700&family=Josefin+Sans:wght@300&family=Cinzel:wght@700&family=Alfa+Slab+One&family=Bebas+Neue&display=swap">
<style>
  :root {
    --teal-dark: #1d5c5a;
    --teal-bright: #1ba8a2;
    --green: #8cc43f;
    --rule: #c8c8c8;
    --paper: #ffffff;
  }
  * { margin: 0; padding: 0; box-sizing: border-box; }
  html, body { width: 858px; height: 1200px; overflow: hidden; background: var(--paper); }
  .manifesto { position: relative; width: 858px; height: 1200px; overflow: hidden; }
  .line { position: absolute; white-space: nowrap; line-height: 1; }
  .rule { position: absolute; height: 6px;
    background: repeating-linear-gradient(135deg, var(--rule) 0 1.5px, transparent 1.5px 4px); }

  .display { font-family: "Righteous", sans-serif; color: var(--teal-bright); text-transform: uppercase; }
  .condensed { font-family: "Oswald", sans-serif; text-transform: uppercase; }
  .rounded { font-family: "Comfortaa", sans-serif; }
  .thin { font-family: "Josefin Sans", sans-serif; font-weight: 300; text-transform: uppercase; }
  .serif-caps { font-family: "Cinzel", serif; font-weight: 700; color: var(--teal-dark); }
  .poster { font-family: "Bebas Neue", sans-serif; color: var(--teal-dark); }
  .slab { font-family: "Alfa Slab One", serif; color: var(--teal-dark); }

  .headline-nurse { left: 18px; top: 18px; font-size: 60px; letter-spacing: 1px; }
  .headline-hands { left: 18px; top: 86px; font-size: 54px; }
  .headline-hearts { left: 18px; top: 140px; font-size: 45px; }

  .self-care { left: 388px; top: 20px; font-family: "Comfortaa", sans-serif; font-size: 16px; color: var(--teal-dark); line-height: 1.45; }
  .delight { left: 388px; top: 84px; font-size: 30px; font-weight: 600; color: var(--green); line-height: 1.13; }

  .support { left: 18px; top: 204px; font-size: 34px; font-weight: 300; color: var(--teal-dark); line-height: 1.08; }
  .respect-word { left: 463px; top: 172px; font-family: "Oswald", sans-serif; font-weight: 600; color: var(--teal-dark); font-size: 66px; letter-spacing: 22px; }
  .respect-text { left: 466px; top: 242px; font-size: 15.5px; font-weight: 700; color: var(--teal-dark); line-height: 1.4; }

  .learn-day { left: 18px; top: 298px; font-size: 47px; letter-spacing: 1px; }
  .trust { left: 18px; top: 355px; font-size: 22.5px; color: var(--green); }

  .lifelong { left: 18px; top: 396px; font-size: 64px; }
  .learner { left: 18px; top: 446px; font-size: 100px; }
  .celebrate { left: 316px; top: 412px; font-size: 34px; font-weight: 300; color: var(--teal-dark); line-height: 1.1; letter-spacing: 1.5px; }

  .smile { left: 18px; top: 527px; font-size: 24.5px; color: var(--green); }

  .right-thing { left: 18px; top: 582px; width: 330px; }
  .right-thing span { display: block; }
  .right-thing .big { font-size: 50px; line-height: 52px; }
  .right-thing .mid { font-size: 31px; line-height: 44px; }
  .right-thing .small { font-size: 25px; line-height: 38px; }
  .unique { left: 365px; top: 574px; font-size: 41px; line-height: 1.1; }
  .within { left: 366px; top: 676px; font-family: "Josefin Sans", sans-serif; font-size: 20px; color: var(--green); text-transform: uppercase; }

  .solution { left: 18px; top: 728px; font-size: 48px; color: var(--teal-bright); letter-spacing: 2px; transform: scaleY(1.4); transform-origin: left top; }

  .follow { left: 18px; top: 810px; font-size: 33px; font-weight: 600; color: var(--green); }
  .lead-purpose { left: 18px; top: 870px; font-family: "Cinzel", serif; font-size: 14px; font-weight: 700; color: var(--teal-bright); }
  .respond { left: 18px; top: 914px; font-size: 24px; color: var(--green); line-height: 1.25; }
  .choose { left: 18px; top: 1034px; font-family: "Cinzel", serif; font-size: 21px; font-weight: 700; color: var(--teal-bright); line-height: 1.5; }
  .choose .minor { font-size: 17px; }
  .live { left: 18px; top: 1064px; font-size: 72px; }
  .live .dream { font-size: 115px; }

  .no-one { left: 546px; top: 812px; font-family: "Comfortaa", sans-serif; font-size: 26px; color: var(--teal-dark); line-height: 1.35; }
  .lead-word { left: 544px; top: 880px; font-size: 80px; transform: scaleY(1.3); transform-origin: left top; }
  .can-do { left: 546px; top: 1000px; font-size: 23px; font-weight: 300; color: var(--green); line-height: 1.6; letter-spacing: 1px; }
  .can-do u { text-underline-offset: 5px; }

  .brand { position: absolute; display: flex; align-items: center; gap: 6px; font-family: "Comfortaa", sans-serif; font-weight: 700; color: var(--teal-dark); font-size: 13px; line-height: 1.15; }
  .brand .dot { width: 14px; height: 14px; border-radius: 50%; background: var(--teal-bright); flex: none; }
  .brand-partner { left: 580px; top: 1130px; }
  .brand-client { left: 745px; top: 1130px; }
</style>
</head>
<body>
<main class="manifesto">
  <div class="line display headline-nurse">Nurse with</div>
  <div class="line display headline-hands">Open hands,</div>
  <div class="line display headline-hearts">Hearts &amp; minds</div>

  <p class="line self-care">Look after YOURSELF &amp; VALUE YOUR HEALTH<br>as much as you value the HEALTH OF OTHERS</p>
  <p class="line condensed delight">Delight your clients &amp; colleagues<br>by exceeding their expectations</p>

  <div class="rule" style="left:18px; top:188px; width:424px;"></div>

  <p class="line condensed support">Support your colleagues and<br>champion their purpose.</p>
  <div class="line respect-word">RESPECT</div>
  <p class="line rounded respect-text">the limits of people's KNOWLEDGE &amp;<br>SHARE YOUR knowledge generously.</p>

  <div class="rule" style="left:18px; top:286px; width:822px;"></div>

  <div class="line display learn-day">Learn something new each day</div>
  <p class="line rounded trust">Trust your knowledge &amp; seek advice only from respected sources.</p>

  <div class="rule" style="left:18px; top:388px; width:822px;"></div>

  <div class="line poster lifelong">BE A LIFELONG</div>
  <div class="line poster learner">LEARNER</div>
  <p class="line condensed celebrate">Celebrate, respect and value the<br>diversity of Australian culture.</p>

  <div class="rule" style="left:316px; top:506px; width:524px;"></div>

  <p class="line rounded smile">SMILE &amp; INFECT others with your HAPPINESS &amp; have FUN!</p>

  <div class="rule" style="left:18px; top:566px; width:822px;"></div>

  <div class="line serif-caps right-thing">
    <span class="big">ALWAYS DO</span>
    <span class="mid">THE RIGHT THING</span>
    <span class="small">WITH OUT EXCEPTION</span>
  </div>
  <div class="line display unique">You are unique revel<br>in your individuality</div>
  <div class="line within">[Seek success firstly from within.]</div>

  <div class="rule" style="left:18px; top:712px; width:822px;"></div>

  <div class="line thin solution">Always be solution focused</div>

  <div class="rule" style="left:18px; top:796px; width:822px;"></div>

  <div class="line condensed follow">Only follow exceptional leaders.</div>
  <div class="rule" style="left:18px; top:854px; width:505px;"></div>
  <div class="line lead-purpose">ALWAYS LEAD WITH PURPOSE, PASSION &amp; COMMITMENT.</div>
  <div class="rule" style="left:18px; top:898px; width:505px;"></div>
  <p class="line rounded respond">“RESPOND to complex situations<br>INNOVATIVELY, CREATIVELY &amp; SAFELY<br>within the scope of your practice.”</p>
  <div class="rule" style="left:18px; top:1018px; width:505px;"></div>
  <p class="line choose">CHOOSE <span class="minor">your thoughts wisely, they create</span><br>YOUR REALITY.</p>
  <div class="line poster live">LIVE YOUR <span class="dream">DREAM</span></div>

  <p class="line no-one">IF THERE IS NO ONE<br>left to follow, then</p>
  <div class="line slab lead-word">LEAD!</div>
  <div class="rule" style="left:546px; top:990px; width:294px;"></div>
  <p class="line condensed can-do">Adopt a <u>‘can do’</u> attitude<br>to <u>everything</u> that comes<br><u>your way.</u></p>

  <div class="brand brand-partner"><span class="dot"></span><span>Care Growth<br>Partners</span></div>
  <div class="brand brand-client"><span class="dot"></span><span>CalmPeak</span></div>
</main>
</body>
</html>
```